Flat bootstrap design for existing site

I'm looking for a modern flat design based around an existing logo. This has to be a custom design (no external templates), and implemented into a bootstrap framework.

The logo is attached as 2 versions - choose whichever you want, that flows better with whatever design you choose.

Added screenshots of the existing site (currently using the default bootstrap layouts). Please make your designs around those pages in the screenshots (i.e. the homepage only has the postal code input and the header). The active page has 3 screenshots, because I wanted to illustrate the other states that would be visible (in the table rows).

This is a moving/junk removal website, just for some context.

Here's some example websites (flat designs) that I like, just to give you an idea of what I'm after.

https://www.plimvora.com/
https://dacklow.com/
https://trevanu.com/
https://quobrintal.com/en/

Coding

Coded - Design and coding required

Number of Pages Required

5+ page

Colors

Designer to choose colors to be used in the design.

Requirements
Must have
• It must be a modern/simple flat design, that is built around the existing logo (attached).
• It has to be implemented using bootstrap.

```html
<!DOCTYPE html>
<html lang="en">
<head>
<meta charset="utf-8">
<title>HAULVEE — Become a Driver</title>
<link rel="stylesheet" href="https://fonts.googleapis.com/css2?family=Montserrat:wght@400;700&family=Roboto:wght@400;500&display=swap">
<style>
:root{
  --sky:#38bdf2;
  --sky-deep:#1287d1;
  --violet:#5b55c6;
  --heading:#5a54b5;
  --ink:#3a3a48;
  --muted:#9a9aa6;
  --line:#d8d8e4;
  --white:#ffffff;
  --hill:#8fd6f6;
}
*{box-sizing:border-box;margin:0;padding:0}
html,body{width:1200px;height:858px;overflow:hidden}
body{position:relative;background:var(--sky);font-family:"Roboto",sans-serif;color:var(--ink)}
.site-header{position:absolute;left:144px;top:0;width:912px;height:80px}
.brand{position:absolute;left:0;top:22px;display:flex;align-items:center;gap:8px;font-family:"Montserrat",sans-serif;font-weight:700;font-size:28px;color:var(--white);letter-spacing:1px}
.brand-dot{width:14px;height:14px;border-radius:50%;background:var(--white)}
.main-nav{position:absolute;right:0;top:22px;display:flex;align-items:center;font-family:"Montserrat",sans-serif;font-weight:700;font-size:11px;letter-spacing:.5px;color:var(--white)}
.main-nav a{color:inherit;text-decoration:none}
.nav-link{margin-right:26px;line-height:35px}
.nav-link + .nav-link{margin-right:24px}
.btn-nav{height:35px;line-height:35px;padding:0 12px;border-radius:2px}
.btn-driver{background:var(--sky-deep);margin-right:8px}
.btn-signin{background:var(--violet);padding:0 19px}
.form-card{position:absolute;left:144px;top:102px;width:912px;height:597px;background:var(--white);border-radius:3px;box-shadow:0 4px 14px rgba(0,40,90,.12)}
.form-title{position:absolute;left:23px;top:26px;font-weight:400;font-size:20px;color:var(--heading)}
.field{position:absolute;left:0;width:444px;height:36px}
.field label{position:absolute;left:0;width:68px;top:50%;transform:translateY(-50%);text-align:right;font-weight:500;font-size:12px;line-height:13px;color:var(--ink)}
.input{position:absolute;left:78px;top:0;width:366px;height:36px;border:1px solid var(--line);border-radius:2px;padding-left:11px;font-family:"Montserrat",sans-serif;font-size:12px;line-height:34px;color:var(--muted)}
.input.focused{border-color:var(--violet)}
.input.select{color:var(--ink)}
.select-caret{position:absolute;right:8px;top:9px}
.btn-apply{position:absolute;left:78px;top:529px;width:81px;height:36px;background:var(--violet);color:var(--white);border:0;border-radius:2px;font-family:"Montserrat",sans-serif;font-weight:700;font-size:11px;letter-spacing:.5px}
.radius-box{position:absolute;left:468px;top:85px;width:420px;height:130px;border:1px solid var(--line);border-radius:2px}
.radius-box p{position:absolute;left:23px;top:24px;width:330px;font-size:14.5px;line-height:19px;color:var(--ink)}
.radius-box .input{left:24px;top:72px;width:134px}
.scene{position:absolute;left:1010px;top:630px;width:190px;height:163px}
.site-footer{position:absolute;left:0;top:793px;width:1200px;height:58px;background:var(--white)}
.copyright{position:absolute;left:144px;top:24px;font-size:12px;color:var(--ink)}
.social{position:absolute;left:987px;top:23px;display:flex;gap:7px}
.social span{width:18px;height:18px;border-radius:2px;background:#8d8bb8}
.footer-band{position:absolute;left:0;top:851px;width:1200px;height:7px;background:var(--violet)}
</style>
</head>
<body>
<header class="site-header">
  <div class="brand"><span class="brand-dot"></span>HAULVEE</div>
  <nav class="main-nav">
    <a class="nav-link" href="#">BOOK</a>
    <a class="nav-link" href="#">HOW IT WORKS</a>
    <a class="btn-nav btn-driver" href="#">BECOME A DRIVER</a>
    <a class="btn-nav btn-signin" href="#">SIGNIN</a>
  </nav>
</header>

<main class="form-card">
  <h1 class="form-title">Interested in becoming a driver? Complete this form, and we’ll assess it and get back to you.</h1>
  <div style="position:absolute;left:0;top:0">
    <div class="field" style="top:85px"><label>First<br>Name</label><div class="input focused">First Name</div></div>
    <div class="field" style="top:133px"><label>Last<br>Name</label><div class="input">Last Name</div></div>
    <div class="field" style="top:181px"><label>Email</label><div class="input">Email</div></div>
    <div class="field" style="top:229px"><label>Password</label><div class="input">Create Password</div></div>
    <div class="field" style="top:277px"><label>Phone</label><div class="input">Phone</div></div>
    <div class="field" style="top:325px"><label>Address</label><div class="input">Address</div></div>
    <div class="field" style="top:373px"><label>City</label><div class="input">City</div></div>
    <div class="field" style="top:421px"><label>Province</label><div class="input select">Ontario
      <svg class="select-caret" width="10" height="16" viewBox="0 0 10 16"><path d="M1 6l4-4 4 4M1 10l4 4 4-4" fill="none" stroke="#5b55c6" stroke-width="1.4"/></svg></div></div>
    <div class="field" style="top:469px"><label>Postal<br>Code</label><div class="input">Postal Code</div></div>
    <button class="btn-apply">APPLY</button>
  </div>
  <section class="radius-box">
    <p>How many km away from your home do you want to service?</p>
    <div class="input">Kilometers</div>
  </section>
</main>

<svg class="scene" role="img" aria-label="Illustration of a mover beside a house and a branded moving van" viewBox="0 0 190 163">
  <path d="M0 163 C10 60 90 10 190 10 L190 163 Z" fill="var(--hill)"/>
  <rect x="40" y="40" width="70" height="55" fill="#7cc7ee"/>
  <rect x="130" y="75" width="60" height="45" rx="4" fill="#2f9fe0"/>
  <rect x="45" y="95" width="30" height="40" fill="#5aaed8"/>
</svg>

<footer class="site-footer">
  <p class="copyright">© 2017 HAULVEE. All rights reserved.</p>
  <div class="social"><span></span><span></span><span></span></div>
</footer>
<div class="footer-band"></div>
</body>
</html>
```